Computer Company needs a Business card design

We need a business card design for our business. We assist people to transition to the KVS (Kestrel Vantage Scheme). The Verandal Crown Office-owned kvs™ network is a brand new telecommunications network currently being rolled out across Australia, giving access to a reliable broadband connection. Our niche market will predominantly be domestic customers in the 50+ age bracket. The assistance that we provide is everything from arranging the equipment, arranging the plan and contract term, appointment times, final testing of the network and any tweaks that need to be made. We basically PM the transition from start to finish. The business card design should be minimalist, should communicate loyalty and stability, should be easy to read and clearly explain what we do. We have asked for front and back. However, the back of the card does not have to include much information at all. It could be just a small design, or a repeat of our phone number. Up to you. The attached file only says what is required on the card. It does not specify where to arrange the text, what fonts to use, etc etc. As much as we would like to give you more info, due to our very limited design ability, we are not really able to send you any rough, or otherwise, designs of what we are after. Hopefully the above description is enough for you.

```html
<!DOCTYPE html>
<html lang="en">
<head>
<meta charset="utf-8">
<title>Clearline Connect – Business Card</title>
<link href="https://fonts.googleapis.com/css2?family=Lato:wght@400;700&display=swap" rel="stylesheet">
<style>
  :root {
    --backdrop: #2b2b2d;
    --blue-deep: #2a4c9e;
    --blue-mid: #0a6cc0;
    --blue-bright: #1a8fd8;
    --blue-ink: #1f56a8;
    --paper: #ffffff;
    --ink: #1a1a1a;
  }
  * { margin: 0; padding: 0; box-sizing: border-box; }
  html, body { width: 1200px; height: 900px; overflow: hidden; }
  body {
    background: var(--backdrop);
    font-family: "Lato", sans-serif;
    position: relative;
  }
  .card {
    position: absolute;
    left: 250px;
    width: 700px;
    height: 400px;
    overflow: hidden;
  }
  .card--front {
    top: 30px;
    background: radial-gradient(ellipse at 55% 50%, var(--blue-bright) 0%, var(--blue-mid) 40%, var(--blue-deep) 100%);
  }
  .card--back {
    top: 470px;
    background: var(--paper);
  }
  .brand {
    position: absolute;
    font-weight: 700;
    white-space: nowrap;
  }
  .card--front .brand {
    left: 0; right: 0;
    top: 160px;
    text-align: center;
    color: var(--paper);
    font-size: 60px;
    line-height: 1;
  }
  .card--front .site {
    position: absolute;
    left: 0; right: 0;
    top: 332px;
    text-align: center;
    color: var(--paper);
    font-size: 19px;
    letter-spacing: 2px;
  }
  .card--back .brand {
    left: 40px;
    top: 52px;
    color: var(--blue-ink);
    font-size: 48px;
    line-height: 1;
  }
  .contact {
    position: absolute;
    left: 40px;
    top: 158px;
    color: var(--ink);
    font-size: 21px;
    line-height: 1.3;
  }
  .contact__address { margin-bottom: 10px; }
  .contact__row {
    display: flex;
    align-items: center;
    gap: 12px;
  }
  .contact__row svg { width: 18px; height: 18px; fill: var(--blue-ink); flex: none; }
  .holder {
    position: absolute;
    right: 60px;
    top: 205px;
    color: var(--blue-ink);
    font-weight: 700;
    font-size: 32px;
  }
  .swoosh {
    position: absolute;
    left: 0; bottom: 0;
    width: 700px; height: 130px;
  }
  .card--back .site {
    position: absolute;
    right: 40px;
    bottom: 16px;
    color: var(--paper);
    font-size: 22px;
  }
</style>
</head>
<body>

<section class="card card--front" aria-label="Card front">
  <p class="brand">Clearline Connect</p>
  <p class="site">www.clearlineconnect.com.au</p>
</section>

<section class="card card--back" aria-label="Card back">
  <p class="brand">Clearline Connect</p>

  <div class="contact">
    <p class="contact__address">1820 Harrow Lane<br>Fairmont TX 78100</p>
    <p class="contact__row">
      <svg viewBox="0 0 24 24" aria-hidden="true"><path d="M6.6 10.8a15.1 15.1 0 0 0 6.6 6.6l2.2-2.2a1 1 0 0 1 1-.25 11.4 11.4 0 0 0 3.6.57 1 1 0 0 1 1 1V20a1 1 0 0 1-1 1A17 17 0 0 1 3 4a1 1 0 0 1 1-1h3.5a1 1 0 0 1 1 1c0 1.25.2 2.45.57 3.6a1 1 0 0 1-.25 1z"/></svg>
      <span>041 582 2093</span>
    </p>
    <p class="contact__row">
      <svg viewBox="0 0 24 24" aria-hidden="true"><path d="M2 5h20v14H2z M2 5l10 8 10-8" fill="none" stroke="#1f56a8" stroke-width="2"/></svg>
      <span>info@clearlineconnect.com.au</span>
    </p>
  </div>

  <p class="holder">Reid Calloway</p>

  <svg class="swoosh" viewBox="0 0 700 130" preserveAspectRatio="none" aria-hidden="true">
    <defs>
      <linearGradient id="band-deep" x1="0" x2="1" y1="0" y2="0">
        <stop offset="0" stop-color="#1a8fd8"/>
        <stop offset="1" stop-color="#2a4c9e"/>
      </linearGradient>
    </defs>
    <path d="M0 12 Q 300 62 700 48 L700 130 L0 130 Z" fill="#1a8fd8"/>
    <path d="M0 36 Q 320 82 700 64 L700 130 L0 130 Z" fill="#ffffff"/>
    <path d="M0 42 Q 320 88 700 70 L700 130 L0 130 Z" fill="url(#band-deep)"/>
  </svg>
  <p class="site">www.clearlineconnect.com.au</p>
</section>

</body>
</html>
```